Business Card Design

New business card design

Target Market(s)

Residential & Commercial Property Managers

Industry/Entity Type

Plumbing Services

Contact Information for Business Card

Name - Rowan Keddle, title - Director, Phone Number - 0431 286 517, email - rowan@tbk-plumbing.com.au, Company ABN - 73 215 904 386,

Font styles to use
Sans Serif

Colors
0054AA
0677BA
7BADD7
CADEEF
E8F1F8

```html
<!DOCTYPE html>
<html lang="en">
<head>
<meta charset="utf-8">
<title>TBK Plumbing – Business Card</title>
<link rel="stylesheet" href="https://fonts.googleapis.com/css2?family=Montserrat:wght@400;600;700&display=swap">
<style>
  :root {
    --stage: #2a2a2b;
    --card-top: #232932;
    --card-bottom: #1b2027;
    --accent: #2ea3e0;
    --accent-deep: #0677ba;
    --text-light: #e8f1f8;
    --text-muted: #9aa3ad;
    --mark-shade: #141a21;
  }
  * { box-sizing: border-box; margin: 0; padding: 0; }
  html, body { width: 1200px; height: 900px; overflow: hidden; }
  body {
    background: var(--stage);
    font-family: "Montserrat", sans-serif;
    position: relative;
  }
  .card {
    position: absolute;
    top: 295px;
    width: 540px;
    height: 310px;
    border-radius: 18px;
    background: linear-gradient(160deg, var(--card-top), var(--card-bottom));
    overflow: hidden;
    box-shadow: 0 18px 40px rgba(0,0,0,.45);
  }
  .card::after {
    content: "";
    position: absolute;
    left: 0; right: 0; bottom: 0;
    height: 9px;
    background: var(--accent);
  }
  .card--front { left: 40px; }
  .card--back { left: 620px; }

  .brand {
    position: absolute;
    display: flex;
    align-items: center;
    gap: 12px;
    color: var(--text-light);
    font-weight: 600;
    letter-spacing: 1px;
  }
  .brand__dot {
    border-radius: 50%;
    background: var(--accent);
    flex: none;
  }
  .card--front .brand {
    left: 0; right: 0; top: 122px;
    justify-content: center;
    font-size: 44px;
  }
  .card--front .brand__dot { width: 22px; height: 22px; }

  .card--back .brand {
    left: 34px; top: 92px;
    font-size: 34px;
  }
  .card--back .brand__dot { width: 17px; height: 17px; }

  .corner-block {
    position: absolute;
    top: 0; right: 0;
    width: 22px; height: 42px;
    background: var(--accent);
  }
  .holder {
    position: absolute;
    top: 20px; right: 40px;
    text-align: right;
  }
  .holder__name {
    color: var(--accent);
    font-weight: 700;
    font-size: 21px;
  }
  .holder__title {
    color: var(--text-light);
    font-size: 12px;
    margin-top: 1px;
  }
  .backdrop-mark {
    position: absolute;
    right: 28px; top: 92px;
    width: 170px; height: 170px;
    border-radius: 50%;
    background: radial-gradient(circle at 35% 30%, #2a3a52, var(--mark-shade) 70%);
  }

  .contact {
    position: absolute;
    left: 34px; top: 172px;
    color: var(--text-light);
    font-size: 12.5px;
    line-height: 1.35;
  }
  .contact__address { margin-bottom: 8px; }
  .contact__row {
    display: flex;
    align-items: center;
    gap: 9px;
    margin-bottom: 4px;
  }
  .contact__row svg { width: 13px; height: 13px; flex: none; fill: var(--accent); }
  .contact__abn { margin-top: 3px; }
  .contact__abn-label { color: var(--accent); font-weight: 700; }
</style>
</head>
<body>

  <section class="card card--front" aria-label="Business card front">
    <div class="brand"><span class="brand__dot"></span>tbk plumbing</div>
  </section>

  <section class="card card--back" aria-label="Business card back">
    <div class="corner-block"></div>
    <div class="holder">
      <div class="holder__name">Rowan Keddle</div>
      <div class="holder__title">Director</div>
    </div>
    <div class="backdrop-mark"></div>

    <div class="brand"><span class="brand__dot"></span>tbk plumbing</div>

    <div class="contact">
      <p class="contact__address">48 Harlow Creek Road<br>Bendale, QLD 4215</p>
      <p class="contact__row">
        <svg viewBox="0 0 24 24" aria-hidden="true"><path d="M6.6 10.8a15.1 15.1 0 0 0 6.6 6.6l2.2-2.2a1 1 0 0 1 1-.25 11.4 11.4 0 0 0 3.6.57 1 1 0 0 1 1 1V20a1 1 0 0 1-1 1A17 17 0 0 1 3 4a1 1 0 0 1 1-1h3.5a1 1 0 0 1 1 1c0 1.25.2 2.45.57 3.57a1 1 0 0 1-.25 1z"/></svg>
        0431 286 517
      </p>
      <p class="contact__row">
        <svg viewBox="0 0 24 24" aria-hidden="true"><path d="M2 5h20v14H2z M4 7v.5l8 5 8-5V7l-8 5z" fill-rule="evenodd"/></svg>
        rowan@tbk-plumbing.com.au
      </p>
      <p class="contact__row">
        <svg viewBox="0 0 24 24" aria-hidden="true"><path d="M12 2a10 10 0 1 0 0 20 10 10 0 0 0 0-20zm0 2c.9 0 2.2 2 2.7 5H9.3C9.8 6 11.1 4 12 4zM4.3 11h3a17 17 0 0 0 0 2h-3a8 8 0 0 1 0-2zm5 0h5.4a15 15 0 0 1 0 2H9.3a15 15 0 0 1 0-2zm7.4 0h3a8 8 0 0 1 0 2h-3a17 17 0 0 0 0-2zM9.3 15h5.4c-.5 3-1.8 5-2.7 5s-2.2-2-2.7-5z"/></svg>
        www.tbk-plumbing.com.au
      </p>
      <p class="contact__abn"><span class="contact__abn-label">ABN</span> - 73 215 904 386</p>
    </div>
  </section>

</body>
</html>
```